Business Card Design Project

Business Card
We are rebranding with a new logo
Industry/Entity Type
Business
Contact Information for Business Card
Dennis Morvale +61 487215963 dennis@quorv.com.au P.O. Box 872 Fernlow QLD 4309
Requirements
Must have
- Logo

```html
<!DOCTYPE html>
<html lang="en">
<head>
<meta charset="UTF-8">
<title>Quorv International – Business Card</title>
<link href="https://fonts.googleapis.com/css2?family=Roboto:wght@400;500&family=Roboto+Condensed:wght@700&display=swap" rel="stylesheet">
<style>
  :root {
    --backdrop: #2b2b2b;
    --card-blue-light: #02a6dc;
    --card-blue-mid: #0883b3;
    --card-blue-dark: #045877;
    --card-white: #ffffff;
    --text-light: #ffffff;
    --brand-blue: #0b73a0;
  }
  html, body {
    margin: 0;
    padding: 0;
    width: 1200px;
    height: 960px;
    overflow: hidden;
    background: var(--backdrop);
  }
  .card {
    position: absolute;
    left: 314px;
    top: 294px;
    width: 600px;
    height: 342px;
    border-radius: 22px;
    overflow: hidden;
    background: radial-gradient(circle at 306px 156px, var(--card-blue-light) 0%, var(--card-blue-mid) 45%, var(--card-blue-dark) 100%);
    font-family: "Roboto", Arial, sans-serif;
    color: var(--text-light);
  }
  .card__sweep {
    position: absolute;
    inset: 0;
    width: 600px;
    height: 342px;
  }
  .card__name {
    position: absolute;
    left: 40px;
    top: 34px;
    margin: 0;
    font-family: "Roboto Condensed", "Arial Narrow", sans-serif;
    font-weight: 700;
    font-size: 21px;
    letter-spacing: 0.2px;
    text-transform: uppercase;
  }
  .card__address {
    position: absolute;
    left: 40px;
    top: 101px;
    margin: 0;
    font-style: normal;
    font-size: 14px;
    line-height: 19px;
  }
  .card__contacts {
    position: absolute;
    left: 40px;
    top: 144px;
    margin: 0;
    padding: 0;
    list-style: none;
    font-size: 14px;
    line-height: 19px;
  }
  .card__contacts li {
    display: flex;
    align-items: center;
    gap: 8px;
  }
  .card__contacts svg {
    width: 14px;
    height: 14px;
    fill: var(--text-light);
    flex: none;
  }
  .brand {
    position: absolute;
    right: 38px;
    top: 214px;
    text-align: right;
    color: var(--brand-blue);
    font-family: "Roboto", Arial, sans-serif;
    font-weight: 500;
  }
  .brand__name {
    display: block;
    font-size: 56px;
    line-height: 60px;
    letter-spacing: 1px;
  }
  .brand__tag {
    display: block;
    margin-top: 6px;
    font-size: 17px;
    letter-spacing: 3.6px;
  }
</style>
</head>
<body>
  <div class="card">
    <svg class="card__sweep" viewBox="0 0 600 342" aria-hidden="true">
      <path d="M216 342 C 300 170 420 112 600 84 L600 342 Z" fill="var(--card-white)"/>
    </svg>

    <h1 class="card__name">Dennis Morvale</h1>

    <address class="card__address">
      P.O. Box 872<br>
      Fernlow QLD 4309
    </address>

    <ul class="card__contacts">
      <li>
        <svg viewBox="0 0 24 24"><path d="M6.6 10.8a15.1 15.1 0 0 0 6.6 6.6l2.2-2.2c.3-.3.7-.4 1-.2 1.1.4 2.3.6 3.6.6.6 0 1 .4 1 1V20c0 .6-.4 1-1 1A17 17 0 0 1 3 4c0-.6.4-1 1-1h3.5c.6 0 1 .4 1 1 0 1.3.2 2.5.6 3.6.1.3 0 .7-.2 1z"/></svg>
        <span>+61 487215963</span>
      </li>
      <li>
        <svg viewBox="0 0 24 24"><path d="M2 5h20v14H2z M3.5 6.5 12 13l8.5-6.5" fill="none" stroke="#fff" stroke-width="0"/><path d="M2 5h20v2.2l-10 6.6L2 7.2z"/><path d="M2 9.4l10 6.6 10-6.6V19H2z"/></svg>
        <span>dennis@quorv.com.au</span>
      </li>
      <li>
        <svg viewBox="0 0 24 24"><path d="M12 2a10 10 0 1 0 0 20 10 10 0 0 0 0-20zm-1 17.9A8 8 0 0 1 4.2 10.2L9 15v1c0 1.1.9 2 2 2zm6.9-2.5c-.3-.8-1-1.4-1.9-1.4h-1v-3c0-.6-.4-1-1-1H8v-2h2c.6 0 1-.4 1-1V7h2c1.1 0 2-.9 2-2v-.4a8 8 0 0 1 2.9 12.8z"/></svg>
        <span>www.quorv.com.au</span>
      </li>
    </ul>

    <div class="brand">
      <span class="brand__name">Quorv</span>
      <span class="brand__tag">INTERNATIONAL</span>
    </div>
  </div>
</body>
</html>
```